Institute for Hip Wellness at Brightwater
business card and stationary
Institute for Hip Wellness at Brightwater -
Creative Brief
Professional
Gordon T. Sleet, MD
482 Fennick Lane, Suite 207 Brightwater, MD 21409
gtsleet82@brightmailbox.net
www.hipwellclinic-demo.com
Use new logo Comprehensive Gynecologic Care with Specialization in Chronic Pain Disorders and Minimally Invasive Surgery
Appointment Date and Time: Mon. _______ Tue _____ Wed ______ Thurs_______ Fri_______ _______ AM _______ PM

```html
<!DOCTYPE html>
<html lang="en">
<head>
<meta charset="utf-8">
<title>Institute for Hip Wellness at Brightwater – Business Card</title>
<link rel="stylesheet" href="https://fonts.googleapis.com/css2?family=Didact+Gothic&display=swap">
<style>
  :root {
    --page-bg: #e9e6e2;
    --card-bg: #ffffff;
    --ink: #4a4a4c;
    --ink-soft: #5c5c5e;
    --accent: #b9509b;
    --mark-grey: #5a5a5c;
    --divider: #b8b8ba;
  }
  * { margin: 0; padding: 0; box-sizing: border-box; }
  html, body {
    width: 1200px; height: 780px; overflow: hidden;
    background: var(--page-bg);
    font-family: "Didact Gothic", "Century Gothic", sans-serif;
    color: var(--ink);
  }
  .business-card {
    position: absolute; left: 100px; top: 105px;
    width: 1000px; height: 570px;
    background: var(--card-bg);
    border-radius: 30px;
    box-shadow: 0 10px 30px rgba(0,0,0,0.12);
  }
  .brand {
    position: absolute; left: 150px; top: 70px;
    display: flex; align-items: center; gap: 34px;
  }
  .brand-dot {
    width: 150px; height: 150px; border-radius: 50%;
    background: var(--mark-grey);
  }
  .brand-name {
    color: var(--ink);
    text-transform: uppercase;
    line-height: 1.02;
    font-size: 50px;
    letter-spacing: 0.5px;
  }
  .brand-name span { display: block; }
  .brand-name .brand-line-small {
    font-size: 27px; letter-spacing: 1px;
    margin-top: 6px; padding-left: 40px;
  }
  .practitioner {
    position: absolute; right: 540px; top: 330px;
    text-align: right;
  }
  .practitioner-name {
    color: var(--accent);
    font-size: 31px;
    letter-spacing: 0.5px;
    margin-bottom: 30px;
  }
  .practitioner-address {
    font-style: normal;
    font-size: 19px;
    line-height: 1.5;
    color: var(--ink-soft);
  }
  .divider {
    position: absolute; left: 490px; top: 320px;
    width: 2px; height: 170px;
    background: var(--divider);
  }
  .contact-list {
    position: absolute; left: 515px; top: 318px;
    list-style: none;
    font-size: 19px; color: var(--ink-soft);
  }
  .contact-list li {
    display: flex; align-items: center; gap: 10px;
    height: 38px;
  }
  .contact-icon { width: 22px; height: 22px; flex: none; fill: var(--accent); }
  .at-icon {
    width: 22px; text-align: center;
    color: var(--accent); font-size: 21px; line-height: 1;
  }
</style>
</head>
<body>
  <section class="business-card">
    <header class="brand">
      <div class="brand-dot"></div>
      <div class="brand-name">
        <span>Institute for</span>
        <span>Hip Wellness</span>
        <span class="brand-line-small">at Brightwater</span>
      </div>
    </header>

    <div class="practitioner">
      <p class="practitioner-name">Gordon T. Sleet, MD</p>
      <address class="practitioner-address">
        482 Fennick Lane, Suite 207<br>
        Brightwater, MD 21409
      </address>
    </div>

    <div class="divider"></div>

    <ul class="contact-list">
      <li>
        <svg class="contact-icon" viewBox="0 0 24 24" aria-hidden="true"><path d="M6.6 10.8a15.1 15.1 0 0 0 6.6 6.6l2.2-2.2c.3-.3.7-.4 1-.2 1.1.4 2.3.6 3.6.6.6 0 1 .4 1 1V20c0 .6-.4 1-1 1C10.6 21 3 13.4 3 4c0-.6.4-1 1-1h3.5c.6 0 1 .4 1 1 0 1.3.2 2.5.6 3.6.1.3 0 .7-.2 1z"/></svg>
        <span>1-855-555-0148</span>
      </li>
      <li>
        <svg class="contact-icon" viewBox="0 0 24 24" aria-hidden="true"><path d="M6.6 10.8a15.1 15.1 0 0 0 6.6 6.6l2.2-2.2c.3-.3.7-.4 1-.2 1.1.4 2.3.6 3.6.6.6 0 1 .4 1 1V20c0 .6-.4 1-1 1C10.6 21 3 13.4 3 4c0-.6.4-1 1-1h3.5c.6 0 1 .4 1 1 0 1.3.2 2.5.6 3.6.1.3 0 .7-.2 1z"/></svg>
        <span>410-555-0136</span>
      </li>
      <li>
        <svg class="contact-icon" viewBox="0 0 24 24" aria-hidden="true"><path d="M7 3h10v5H7zM4 9h16a1 1 0 0 1 1 1v7h-4v4H7v-4H3v-7a1 1 0 0 1 1-1zm5 7v3h6v-3z"/></svg>
        <span>410-555-0142</span>
      </li>
      <li>
        <span class="at-icon" aria-hidden="true">@</span>
        <span>gtsleet82@brightmailbox.net</span>
      </li>
    </ul>
  </section>
</body>
</html>
```